Lantern Petals Website v.1 - attract floral shop franchisees

I need a simple information website for my new business. We are a franchisor of flower shops. The overall purpose of the website is to promote the company and the service, especially to potential franchisees and retailers. Only about 4 pages are required including homepage, About, For Supermarkets, For Franchisees, and Contact. No special functions are required except the site will have two separate inquiry forms that must be filled out online and submitted via automated email. Similarly, an email form should be linked from the Contact page. I have a logo and business cards designed by ArtMingle, and I would like the site to have a consistent color scheme and style. The key to design will be to express the joy and love associated with flowers and floral bouquets.
IMPORTANT - I will be exporting the website design to Wordpress CMS in a site hosted by HostNimbus. For smooth integration into WordPress hosted by HostNimbus, the designer should build the site using a WordPress-friendly format. Ideally, they should use HTML, CSS, and PHP. Creating a custom theme or using a page builder that exports to WordPress-compatible files is best. This ensures the site can be easily imported and managed within WordPress.

Target Market(s)

Potential franchisees (existing florists or creative types who might like to own a floral business) and supermarkets who might want us to run their floral department

Industry/Entity Type

Floral retailing

Requirements
Must have
• A brand theme that is beautiful, consistent throughout and builds on the logo design
Nice to have
• Show gender and ethnic diversity in customers and florists. Pictures of happy florists (for franchisees) and pictures of amazing floral department displays (for supermarkets)

```html
<!DOCTYPE html>
<html lang="en">
<head>
<meta charset="utf-8">
<title>Lantern Petals</title>
<link href="https://fonts.googleapis.com/css2?family=Montserrat:wght@500;600;700;800&family=Lato:wght@400;700&family=Great+Vibes&display=swap" rel="stylesheet">
<style>
:root{
  --green:#1a9148;
  --orange:#f39c21;
  --ink:#111;
  --body:#333;
  --grey-band:#f4f4f4;
  --black:#000;
  --white:#fff;
}
*{box-sizing:border-box;margin:0;padding:0}
html,body{width:1200px;height:3462px;overflow:hidden}
body{position:relative;font-family:"Lato",sans-serif;color:var(--body);background:var(--white)}
.abs{position:absolute}
.head{font-family:"Montserrat",sans-serif}

/* header */
.topbar{left:0;top:0;width:1200px;height:90px;background:var(--white)}
.navband{left:0;top:90px;width:1200px;height:54px;background:var(--green)}
.phoneband{left:905px;top:90px;width:295px;height:54px;background:var(--orange)}
.logo-panel{left:112px;top:0;width:252px;height:132px;background:var(--white);clip-path:polygon(0 0,100% 0,100% 70%,82% 100%,18% 100%,0 70%)}
.brand{display:flex;align-items:center;gap:10px;font-family:"Montserrat",sans-serif;font-weight:700;color:var(--green)}
.brand .dot{width:30px;height:30px;border-radius:50%;background:var(--orange);flex:none}
.header-brand{left:132px;top:30px;font-size:24px}
.info-icon{width:42px;height:42px;border-radius:50%;background:var(--orange);display:flex;align-items:center;justify-content:center}
.info-title{font-family:"Montserrat",sans-serif;font-weight:600;font-size:18px;color:var(--ink)}
.info-sub{font-size:14px;color:#555;line-height:19px}
.nav{top:90px;height:54px;display:flex;align-items:center;font-size:13px;color:var(--white)}
.phone-circle{left:882px;top:96px;width:42px;height:42px;border-radius:50%;background:var(--white);border:3px solid var(--green);display:flex;align-items:center;justify-content:center}
.phone-num{left:940px;top:103px;font-family:"Montserrat",sans-serif;font-weight:600;font-size:20px;color:var(--white)}

/* hero */
.hero{left:0;top:144px;width:1200px;height:624px;background:linear-gradient(100deg,#4a3528 0%,#6b5243 35%,#a07a5c 55%,#d79a7d 70%,#b8886a 85%,#5a4436 100%)}
.hero-welcome{left:110px;top:280px;font-family:"Montserrat",sans-serif;font-weight:700;font-size:26px;color:var(--orange);letter-spacing:.5px}
.hero-script{left:114px;top:318px;font-family:"Great Vibes",cursive;font-size:104px;color:var(--white);line-height:1}
.hero-caps{left:170px;top:440px;font-family:"Montserrat",sans-serif;font-weight:800;font-size:84px;color:var(--white);line-height:1}
.btn{display:flex;align-items:center;justify-content:center;border-radius:6px;font-family:"Montserrat",sans-serif;font-weight:700;font-size:14px}
.btn-orange{background:var(--orange);color:#222}
.btn-green{background:var(--green);color:var(--white)}

/* sections */
.section-title{font-family:"Montserrat",sans-serif;font-weight:700;font-size:36px;color:var(--ink);text-align:center}
.section-text{font-size:16px;line-height:30px;text-align:center;color:var(--body)}
.photo{border-radius:50%}
.about-bg{left:0;top:768px;width:1200px;height:665px;background:radial-gradient(circle at 8% 10%,#fbe4ea 0,transparent 22%),radial-gradient(circle at 95% 50%,#f9dde6 0,transparent 30%),radial-gradient(circle at 20% 95%,#fbe6ec 0,transparent 22%),var(--white)}
.super-bg{left:0;top:1433px;width:1200px;height:630px;background:var(--grey-band)}

/* contact */
.footer-bg{left:0;top:2887px;width:1200px;height:575px;background:var(--black)}
.contact-card{left:105px;top:2715px;width:988px;height:278px;background:var(--green);border-radius:40px}
.contact-title{left:105px;top:2780px;width:988px;text-align:center;font-family:"Montserrat",sans-serif;font-weight:700;font-size:36px;color:var(--white)}
.contact-btn{top:2863px;height:55px;border-radius:5px;font-size:17px}
.btn-white{background:var(--white);color:#111}

/* footer */
.foot-brand{left:114px;top:3140px;font-size:30px;color:var(--orange)}
.social{top:3249px;width:24px;height:24px;border-radius:50%;background:var(--white)}
.social.first{background:var(--orange)}
.foot-head{font-family:"Montserrat",sans-serif;font-weight:700;font-size:19px;color:var(--white)}
.foot-head::after{content:"";display:block;width:40px;height:3px;background:var(--orange);margin-top:8px}
.foot-links{list-style:none;color:var(--white)}
.foot-links li{height:30px}
.foot-text{font-size:16px;line-height:26px;color:var(--white)}
.subscribe{left:755px;top:3219px;width:275px;height:42px;border-radius:21px;background:var(--white)}
.subscribe span{position:absolute;left:20px;top:11px;font-size:15px;color:#999}
.subscribe-btn{position:absolute;right:0;top:0;width:44px;height:42px;border-radius:50%;background:var(--orange);display:flex;align-items:center;justify-content:center}
.divider{left:105px;top:3364px;width:978px;height:1px;background:#333}
.copyright{left:0;top:3400px;width:1200px;text-align:center;font-size:15px;color:var(--white)}
</style>
</head>
<body>

<!-- header -->
<div class="abs topbar"></div>
<div class="abs navband"></div>
<div class="abs phoneband"></div>
<div class="abs logo-panel"></div>
<div class="abs brand header-brand"><span class="dot"></span>Lantern Petals</div>

<div class="abs info-icon" style="left:436px;top:25px">
  <svg width="20" height="16" viewBox="0 0 20 16"><rect x="1" y="1" width="18" height="14" rx="2" fill="#fff"/><path d="M1 2 L10 9 L19 2" stroke="#f39c21" stroke-width="2" fill="none"/></svg>
</div>
<div class="abs" style="left:490px;top:26px">
  <div class="info-title">Send Us Email</div>
  <div class="info-sub">info@lantern-petals.com</div>
</div>
<div class="abs info-icon" style="left:750px;top:25px">
  <svg width="16" height="22" viewBox="0 0 16 22"><path d="M8 0C3.6 0 0 3.5 0 7.8 0 13.5 8 22 8 22s8-8.5 8-14.2C16 3.5 12.4 0 8 0z" fill="#fff"/><circle cx="8" cy="8" r="3" fill="#f39c21"/></svg>
</div>
<div class="abs info-sub" style="left:805px;top:28px;width:270px">14 b lantern-petals Lorem ipsum dolor sit amet, consectetur adipiscing elit</div>

<nav class="abs nav" style="left:390px">About Us</nav>
<nav class="abs nav" style="left:484px">For Supermarkets</nav>
<nav class="abs nav" style="left:638px">For Franchisees</nav>
<nav class="abs nav" style="left:793px">Contact</nav>
<div class="abs phone-circle">
  <svg width="18" height="18" viewBox="0 0 24 24"><path d="M6.6 10.8c1.4 2.8 3.8 5.1 6.6 6.6l2.2-2.2c.3-.3.7-.4 1-.2 1.1.4 2.3.6 3.6.6.6 0 1 .4 1 1V20c0 .6-.4 1-1 1C10.6 21 3 13.4 3 4c0-.6.4-1 1-1h3.5c.6 0 1 .4 1 1 0 1.3.2 2.5.6 3.6.1.3 0 .7-.2 1L6.6 10.8z" fill="#1a9148"/></svg>
</div>
<div class="abs phone-num">100-555-0142</div>

<!-- hero -->
<div class="abs hero" role="img" aria-label="Bouquet of tulips and roses on a wooden florist counter"></div>
<div class="abs hero-welcome">WELCOME TO</div>
<div class="abs hero-script">Lantern</div>
<div class="abs hero-caps">PETALS</div>
<div class="abs btn btn-orange" style="left:112px;top:552px;width:149px;height:51px">GET STARTED</div>

<!-- about -->
<div class="abs about-bg" role="img" aria-label="Soft pink blossom decoration"></div>
<h2 class="abs section-title" style="left:120px;top:898px;width:430px">ABOUT US</h2>
<p class="abs section-text" style="left:115px;top:959px;width:440px">Lantern Petals operates in partnership with Northbay Group, the leading franchisor of sushi stations and pre-packaged fruit &amp; vegetable departments to supermarkets across the United States and United Kingdom.&nbsp; Lantern Petals’ combination of floral and supermarket franchising expertise guarantees that consumers, franchisees and supermarket partners each receive exceptional service and value.</p>
<div class="abs btn btn-orange" style="left:267px;top:1195px;width:150px;height:51px">LERAN MORE</div>
<div class="abs photo" style="left:602px;top:864px;width:430px;height:430px;background:radial-gradient(circle at 50% 45%,#e8c2c6 0,#8a6a5c 45%,#4a3a30 100%)" role="img" aria-label="Florist hands arranging a protea bouquet on a wooden table"></div>

<!-- supermarkets -->
<div class="abs super-bg" role="img" aria-label="Faint leaf pattern background"></div>
<div class="abs photo" style="left:177px;top:1536px;width:430px;height:430px;background:radial-gradient(circle at 50% 65%,#e86a8a 0,#b79a7a 40%,#5e5446 100%)" role="img" aria-label="Supermarket floral department display full of colourful bouquets"></div>
<h2 class="abs section-title" style="left:655px;top:1583px;width:440px">SUPERMARKETS</h2>
<p class="abs section-text" style="left:655px;top:1645px;width:440px">Lantern Petals works with some of the country’s largest and most progressive supermarkets to provide franchisee ownership and operation of their strategically important floral departments.&nbsp; Supermarkets find that Lantern Petals is able to improve their financial outcomes, provide attentive customer service and satisfaction, and lift the quality of the entire store environment.</p>
<div class="abs btn btn-green" style="left:801px;top:1876px;width:149px;height:51px">LERAN MORE</div>

<!-- franchisee -->
<h2 class="abs section-title" style="left:117px;top:2221px;width:460px">FRANCHISEE</h2>
<p class="abs section-text" style="left:110px;top:2286px;width:465px">Lantern Petals brings the best of professional florists and supermarkets together for the benefit of consumers.&nbsp; It supports a national network of owner-operator franchisees, who in many cases are multi-site professional florists, with comprehensive services to enhance franchise profitability.&nbsp; Lantern Petals works with some of the country’s largest and most progressive supermarkets to provide franchisee ownership and operation of their strategically important floral departments</p>
<div class="abs btn btn-green" style="left:263px;top:2554px;width:150px;height:51px">LERAN MORE</div>
<div class="abs photo" style="left:599px;top:2164px;width:430px;height:430px;background:radial-gradient(circle at 50% 55%,#f3a6b8 0,#c9d9a0 45%,#e9e4d6 100%)" role="img" aria-label="Smiling florist holding a bouquet of pink roses and tulips"></div>

<!-- contact -->
<div class="abs footer-bg"></div>
<div class="abs contact-card"></div>
<h2 class="abs contact-title">CONTACT US</h2>
<div class="abs btn contact-btn btn-white" style="left:171px;width:367px">NEW FLORIST FRANCHISE INQUIRY</div>
<div class="abs btn contact-btn btn-orange" style="left:566px;width:461px">PROFESSIONAL FLORIST FRANCHISE INQUIRY</div>

<!-- footer -->
<div class="abs brand foot-brand"><span class="dot"></span>Lantern Petals</div>
<div class="abs social first" style="left:184px"></div>
<div class="abs social" style="left:215px"></div>
<div class="abs social" style="left:245px"></div>
<div class="abs social" style="left:276px"></div>

<div class="abs" style="left:413px;top:3100px">
  <div class="foot-head">QUICK LINK</div>
  <ul class="foot-links" style="margin-top:20px;font-size:16px"><li>About Us</li><li>For Supermarkets</li><li>For Franchisees</li><li>Contact</li></ul>
</div>
<div class="abs" style="left:583px;top:3100px">
  <div class="foot-head">SUPPORT</div>
  <ul class="foot-links" style="margin-top:20px;font-size:14px"><li>Terms &amp; Conditions</li><li>Privacy Policy</li><li>About Us</li><li>Support</li></ul>
</div>
<div class="abs" style="left:754px;top:3100px">
  <div class="foot-head">SUBSCRIBE TO OUR NEWSLETTER</div>
  <p class="foot-text" style="margin-top:16px;width:300px">Lorem ipsum dolor sit amet, consectetur adipiscing elit, sed do</p>
</div>
<div class="abs subscribe">
  <span>Enter Your Email</span>
  <div class="subscribe-btn"><svg width="18" height="18" viewBox="0 0 24 24"><path d="M2 11 L22 2 L14 22 L11 13 Z" fill="#fff"/></svg></div>
</div>
<div class="abs divider"></div>
<div class="abs copyright">©Copyrights 2024 Lantern Petals &nbsp;&nbsp;| &nbsp;&nbsp; All Rights Reserved</div>

</body>
</html>
```